Local Flower Farm Needs Business Card Design

I need business cards designed for a flower farm based in Eudora, Kansas.
Business Info:
We are a local cut flower farm located in Eudora, Kansas, founded by Corinne Haldwick. What started as a passion for agriculture and search for more joy in daily life has blossomed into a small business dedicated to providing the community with beautiful, fresh, and sustainable flowers. We specialize in local, seasonal blooms, ensuring that every petal reflects the care and dedication we pour into our craft. Our mission is to deliver the highest quality flowers directly to our customers through local farmers markets and to florists who share our commitment to sustainability. Join us in celebrating the beauty of nature, one bloom at a time!
Contact Details:
Corinne Haldwick
Owner
Phone 913-555-0147
Facebook: Rosalind Thorpe Gardens
Instagram: @RosalindThorpeGardens
Website: RosalindThorpeGardens.example
Target Market(s)
Wholesale to Florists and Direct to Consumer via Farmers Market
Industry/Entity Type
Florist, Farm
Contact Information for Business Card
Name, Contact Info, Logo
Look and feel
Each slider illustrates characteristics of the customer's brand and the style your logo design should communicate.

```html
<!DOCTYPE html>
<html lang="en">
<head>
<meta charset="utf-8">
<title>Rosalind Thorpe Gardens — Business Card</title>
<link href="https://fonts.googleapis.com/css2?family=Open+Sans:wght@400;700&family=Playfair+Display:wght@500&display=swap" rel="stylesheet">
<style>
  :root {
    --forest: #0f3a3a;
    --forest-deep: #0b2e2f;
    --paper: #ffffff;
    --backdrop: #e9ebea;
    --muted: #c9d3d2;
  }
  * { box-sizing: border-box; margin: 0; padding: 0; }
  html, body { width: 1200px; height: 900px; overflow: hidden; }
  body {
    background: var(--backdrop);
    font-family: "Open Sans", Arial, sans-serif;
    position: relative;
  }
  .card {
    position: absolute;
    left: 285px;
    width: 630px;
    height: 360px;
    overflow: hidden;
    box-shadow: 0 6px 18px rgba(0,0,0,.18);
  }
  .card--front { top: 50px; background: var(--paper); }
  .card--back { top: 490px; background: var(--forest); }

  .brand-seal {
    position: absolute;
    width: 150px; height: 150px;
    border-radius: 50%;
    border: 1.5px solid currentColor;
    display: flex; align-items: center; justify-content: center;
    text-align: center;
    font-family: "Playfair Display", Georgia, serif;
    font-weight: 500;
    font-size: 17px;
    line-height: 1.25;
    letter-spacing: .08em;
    text-transform: uppercase;
    padding: 0 18px;
  }
  .card--front .brand-seal { color: var(--forest); left: 240px; top: 22px; }
  .card--back .brand-seal { color: var(--paper); left: 225px; top: 90px; width: 180px; height: 180px; font-size: 20px; }

  .contact-band {
    position: absolute;
    left: 0; right: 0;
    top: 200px; height: 122px;
    background: var(--forest);
    color: var(--paper);
    display: flex; align-items: center;
  }
  .person {
    width: 250px;
    text-align: right;
    padding-right: 22px;
  }
  .person__name { font-weight: 700; font-size: 22px; }
  .person__role { font-size: 13px; color: var(--muted); margin-top: 4px; }
  .divider { width: 1px; height: 82px; background: var(--muted); }
  .contacts { list-style: none; padding-left: 16px; font-size: 15px; line-height: 1.45; }
  .contacts li { display: flex; align-items: center; gap: 8px; }
  .contacts svg { width: 13px; height: 13px; flex: none; }
</style>
</head>
<body>
  <section class="card card--front" aria-label="Card front">
    <div class="brand-seal">Rosalind Thorpe Gardens</div>
    <div class="contact-band">
      <div class="person">
        <p class="person__name">Corinne Haldwick</p>
        <p class="person__role">Owner</p>
      </div>
      <div class="divider"></div>
      <ul class="contacts">
        <li>
          <svg viewBox="0 0 16 16" aria-hidden="true"><path d="M4 1.5 6.5 4 5 6c1 2 3 4 5 5l2-1.5 2.5 2.5-2 2.5C7 14 2 9 1.5 3.5Z" fill="#fff"/></svg>
          913-555-0147
        </li>
        <li>
          <svg viewBox="0 0 16 16" aria-hidden="true"><circle cx="8" cy="8" r="6" fill="#fff"/></svg>
          Rosalind Thorpe Gardens
        </li>
        <li>
          <svg viewBox="0 0 16 16" aria-hidden="true"><circle cx="8" cy="8" r="6" fill="#fff"/></svg>
          @RosalindThorpeGardens
        </li>
        <li>
          <svg viewBox="0 0 16 16" aria-hidden="true"><g fill="none" stroke="#fff" stroke-width="1.4"><circle cx="8" cy="8" r="6.3"/><ellipse cx="8" cy="8" rx="2.8" ry="6.3"/><path d="M1.7 8h12.6"/></g></svg>
          www.RosalindThorpeGardens.example
        </li>
      </ul>
    </div>
  </section>

  <section class="card card--back" aria-label="Card back">
    <div class="brand-seal">Rosalind Thorpe Gardens</div>
  </section>
</body>
</html>
```